Dynamic Business Card for Sports Supplements Company

Hi! I'm looking for an awesome business card to match my existing sports supplement company. I have uploaded my current company logo and screenshot of the front page of my website.

I would like to have something dynamic and interesting and utilize the colors in the website - the reds and purples

The business card should be double sided and focus on a unique eye-catching design on the back and include all the relevant company info.

Most importantly, it should say somewhere: "Sign up on our website for a coupon code."

Target Market(s)

Mostly for women gym goers but it shouldn't be too feminine. It should be in keeping with the website design. It should flow and clearly be connected to it

Industry/Entity Type

Business

Contact Information for Business Card

Lorraine K. Vestal
CEO
LVestal@Quorvanexco.com
www.quorvanexco.com
555.417.3820
P.O. Box 47315
Elmsbury, Northland 00000

Sign up on our website for a coupon code

Font styles to use
Serif
Sans Serif
Other font styles liked:
• Novecento font family and "Quorvanex" is in AR Destine font

Requirements
Must have
• One side should be a bold Quorvanex logo design. Even just the symbol itself may be o.k. (see attached file)

```html
<!DOCTYPE html>
<html lang="en">
<head>
<meta charset="utf-8">
<title>Quorvanex Business Card</title>
<link rel="stylesheet" href="https://fonts.googleapis.com/css2?family=Open+Sans:wght@400;600;700;800&display=swap">
<style>
  :root {
    --stage: #e9e6e2;
    --card-black: #1d1d1f;
    --card-white: #f3f3f3;
    --brand-red: #e1232e;
    --ink-dark: #262626;
    --ink-light: #f4f4f4;
  }
  * { box-sizing: border-box; margin: 0; padding: 0; }
  html, body {
    width: 1200px; height: 780px; overflow: hidden;
    background: var(--stage);
    font-family: "Open Sans", Arial, sans-serif;
  }
  .sheet {
    width: 1200px; height: 780px;
    display: flex; align-items: center; justify-content: center; gap: 40px;
  }
  .card {
    position: relative; width: 560px; height: 320px; overflow: hidden;
    background: var(--card-black);
    box-shadow: 0 6px 18px rgba(0,0,0,0.18);
  }
  .card-front .divider { position: absolute; inset: 0; }
  .brand-lockup {
    position: absolute; left: 30px; top: 164px;
    display: flex; align-items: center; gap: 10px;
  }
  .brand-mark { width: 18px; height: 18px; background: var(--brand-red); }
  .brand-name {
    font-weight: 800; font-size: 28px; letter-spacing: 1px;
    text-transform: uppercase; color: var(--ink-dark);
  }
  .contact {
    position: absolute; left: 340px; top: 44px; color: var(--ink-light);
  }
  .contact-name { color: var(--brand-red); font-weight: 700; font-size: 21px; line-height: 1.1; }
  .contact-title { font-size: 13px; margin-top: 3px; }
  .contact-address { font-size: 13px; line-height: 1.45; margin-top: 40px; }
  .contact-lines { list-style: none; margin-top: 12px; font-size: 13px; }
  .contact-lines li { display: flex; align-items: center; gap: 8px; height: 22px; }
  .icon-box {
    flex: none; width: 16px; height: 16px; background: var(--brand-red);
    display: flex; align-items: center; justify-content: center;
  }
  .accent { color: var(--brand-red); }

  .card-back .brand-lockup { left: 50%; top: 108px; transform: translateX(-50%); }
  .card-back .brand-name { color: var(--ink-light); font-size: 38px; }
  .card-back .brand-mark { width: 22px; height: 22px; }
  .offer {
    position: absolute; left: 0; right: 0; top: 200px; text-align: center;
    font-size: 17px; color: var(--ink-light);
  }
</style>
</head>
<body>
<main class="sheet">
  <section class="card card-front" aria-label="Card front">
    <svg class="divider" width="560" height="320" viewBox="0 0 560 320" aria-hidden="true">
      <path d="M240 0 C335 55 300 255 430 320 H462 C330 250 360 50 262 0 Z" fill="var(--brand-red)"/>
      <path d="M0 0 H240 C335 55 300 255 430 320 H0 Z" fill="var(--card-white)"/>
    </svg>
    <div class="brand-lockup">
      <span class="brand-mark"></span>
      <span class="brand-name">Quorvanex</span>
    </div>
    <div class="contact">
      <p class="contact-name">Lorraine K. Vestal</p>
      <p class="contact-title">CEO</p>
      <p class="contact-address">P.O. Box 47315<br>Elmsbury, Northland 00000</p>
      <ul class="contact-lines">
        <li>
          <span class="icon-box"><svg width="10" height="10" viewBox="0 0 10 10"><path d="M2 1 L4 1 L4.6 3 L3.4 4 Q4.4 6 6 6.6 L7 5.4 L9 6 L9 8 Q5 9.5 1 5 Q0.5 2.5 2 1Z" fill="#fff"/></svg></span>
          <span>555.417.3820</span>
        </li>
        <li>
          <span class="icon-box"><svg width="10" height="8" viewBox="0 0 10 8"><rect x="0.5" y="0.5" width="9" height="7" fill="none" stroke="#fff"/><path d="M0.5 0.5 L5 4.5 L9.5 0.5" fill="none" stroke="#fff"/></svg></span>
          <span>LVestal@Quorvanexco.com</span>
        </li>
        <li>
          <span class="icon-box"><svg width="10" height="10" viewBox="0 0 10 10"><circle cx="5" cy="5" r="4.3" fill="none" stroke="#fff"/><ellipse cx="5" cy="5" rx="1.8" ry="4.3" fill="none" stroke="#fff"/><path d="M0.7 5 H9.3" stroke="#fff"/></svg></span>
          <span>www.<span class="accent">quorvanexco</span>.com</span>
        </li>
      </ul>
    </div>
  </section>

  <section class="card card-back" aria-label="Card back">
    <div class="brand-lockup">
      <span class="brand-mark"></span>
      <span class="brand-name">Quorvanex</span>
    </div>
    <p class="offer"><span class="accent">Sign up</span> on our website for a coupon code</p>
  </section>
</main>
</body>
</html>
```